Local fast-growing company in the service sector

We are looking for a modern business card design, which should also appear on our letterheads

Target Market(s)

Private and industrial sectors

Contact Information for Business Card

Vorname Name
Kellberger Str. 18
72458 Lindenfeld
Tel.: 07146-839214-0
Name@agentur-kvtl.de

Colors
9d9d9d
919191
aaaaaa

Requirements
Must have
• The logo (file) in silver

```html
<!DOCTYPE html>
<html lang="de">
<head>
<meta charset="utf-8">
<title>KVTL Visitenkarte</title>
<link href="https://fonts.googleapis.com/css2?family=Source+Sans+3:wght@400;600;700&display=swap" rel="stylesheet">
<style>
  :root {
    --bg-top: #f4f4f4;
    --bg-bottom: #dcdcdc;
    --card-white: #ffffff;
    --panel-grey: #d6d6d7;
    --strip-dark: #4a4a4c;
    --strip-mid: #6a6a6c;
    --strip-light: #8a8a8c;
    --pill: #c9c9ca;
    --icon: #5a5a5c;
    --brand: #9d9d9d;
    --text: #555557;
    --name: #4a4a4c;
  }
  * { margin: 0; padding: 0; box-sizing: border-box; }
  html, body { width: 940px; height: 1200px; overflow: hidden; }
  body {
    background: radial-gradient(ellipse at 50% 45%, var(--bg-top), var(--bg-bottom));
    font-family: "Source Sans 3", sans-serif;
    position: relative;
  }
  .card-spread {
    position: absolute;
    left: 56px; top: 364px;
    display: flex; gap: 10px;
  }
  .card {
    width: 409px; height: 472px;
    box-shadow: 0 3px 8px rgba(0,0,0,0.18);
    position: relative;
  }
  .card-front {
    background: var(--card-white);
    display: flex; align-items: center; justify-content: center;
  }
  .brand { display: flex; align-items: center; gap: 14px; margin-top: -46px; }
  .brand-square { width: 44px; height: 44px; background: var(--brand); }
  .brand-name {
    font-weight: 700; font-size: 64px; letter-spacing: 1px;
    color: var(--brand); line-height: 1;
  }
  .card-back { background: var(--panel-grey); }
  .strip {
    position: absolute; left: 0; top: 0; width: 54px; height: 100%;
    background: var(--strip-dark);
  }
  .strip-band { position: absolute; left: 0; width: 100%; }
  .band-1 { top: 0; height: 22px; background: var(--strip-mid); }
  .band-2 { top: 22px; height: 30px; background: var(--strip-light); }
  .band-3 { top: 52px; height: 34px; background: var(--strip-dark); }
  .band-4 { top: 86px; height: 26px; background: var(--strip-mid); }
  .band-5 { top: 360px; height: 36px; background: var(--strip-mid); }
  .band-6 { top: 396px; height: 38px; background: var(--strip-dark); }
  .band-7 { top: 434px; height: 38px; background: var(--strip-light); }
  .icon-pill {
    position: absolute; left: 10px; top: 190px;
    width: 34px; height: 82px; border-radius: 17px;
    background: var(--pill);
    display: flex; flex-direction: column; align-items: center; justify-content: center; gap: 10px;
  }
  .contact {
    position: absolute; left: 70px; top: 150px;
    color: var(--text); font-size: 21px; line-height: 1.3;
  }
  .contact-name { color: var(--name); font-weight: 700; font-size: 27px; margin-bottom: 14px; }
  .contact-address { margin-top: 22px; }
</style>
</head>
<body>
  <div class="card-spread">
    <section class="card card-front">
      <div class="brand">
        <span class="brand-square"></span>
        <span class="brand-name">KVTL</span>
      </div>
    </section>
    <section class="card card-back">
      <div class="strip">
        <span class="strip-band band-1"></span>
        <span class="strip-band band-2"></span>
        <span class="strip-band band-3"></span>
        <span class="strip-band band-4"></span>
        <span class="strip-band band-5"></span>
        <span class="strip-band band-6"></span>
        <span class="strip-band band-7"></span>
        <div class="icon-pill">
          <svg width="16" height="16" viewBox="0 0 24 24" aria-label="Telefon">
            <path fill="var(--icon)" d="M6.6 10.8c1.4 2.8 3.8 5.1 6.6 6.6l2.2-2.2c.3-.3.7-.4 1-.2 1.1.4 2.3.6 3.6.6.6 0 1 .4 1 1V20c0 .6-.4 1-1 1C10.6 21 3 13.4 3 4c0-.6.4-1 1-1h3.5c.6 0 1 .4 1 1 0 1.3.2 2.5.6 3.6.1.3 0 .7-.2 1L6.6 10.8z"/>
          </svg>
          <svg width="16" height="14" viewBox="0 0 24 20" aria-label="E-Mail">
            <rect x="1" y="2" width="22" height="16" rx="2" fill="var(--icon)"/>
            <path d="M2 4l10 7 10-7" fill="none" stroke="var(--pill)" stroke-width="2"/>
          </svg>
        </div>
      </div>
      <div class="contact">
        <p class="contact-name">Vorname Name</p>
        <p class="contact-phone">07146-839214-0</p>
        <p class="contact-email">Name@agentur-kvtl.de</p>
        <div class="contact-address">
          <p>Kellberger Str. 18</p>
          <p>72458 Lindenfeld</p>
        </div>
      </div>
    </section>
  </div>
</body>
</html>
```